Meadowlark Property Review is a leading provider of residential appraisal and home inspection products in S

I need a business card/logo designed that obviously describes my business. We are a residential appraisal and home inspection company in Springfield, MO. We offer residential appraisals, home inspection, pest inspection and radon gas measurement. We have been in business for 18 years and hold state certified residential appraisal licenses and OBREX certified home inspection licenses. I have a logo that I really like and will attach, but would be open to new suggestions. I like more modern designs than traditional and would like a two sided card with our services, licenses and qualifications on the back.

```html
<!DOCTYPE html>
<html lang="en">
<head>
<meta charset="utf-8">
<title>Meadowlark Property Review – Business Card</title>
<link href="https://fonts.googleapis.com/css2?family=PT+Sans:ital,wght@0,400;0,700;1,400&display=swap" rel="stylesheet">
<style>
  :root {
    --stage: #3b3b3b;
    --brown: #8b6b44;
    --orange: #f08a1c;
    --paper: #f7f7f7;
    --ink: #4a4a4a;
    --white: #ffffff;
    --cream: #f3e6d4;
  }
  * { margin: 0; padding: 0; box-sizing: border-box; }
  html, body { width: 1200px; height: 750px; overflow: hidden; }
  body {
    background: var(--stage);
    font-family: "PT Sans", "Helvetica Neue", Arial, sans-serif;
    position: relative;
  }
  .card {
    position: absolute;
    top: 228px;
    width: 461px;
    height: 262px;
    overflow: hidden;
  }
  .card-front { left: 124px; background: var(--paper); }
  .card-back { left: 618px; background: var(--brown); }

  .front-shape { position: absolute; inset: 0; }

  .holder {
    position: absolute;
    right: 30px;
    top: 26px;
    text-align: right;
  }
  .holder-name { color: var(--orange); font-size: 17px; font-weight: 700; line-height: 1.1; }
  .holder-title { color: var(--white); font-size: 12.5px; line-height: 1.4; }

  .brand-name {
    position: absolute;
    left: 34px;
    top: 122px;
    color: var(--brown);
    font-size: 20px;
    font-weight: 700;
    white-space: nowrap;
  }

  .contact-list {
    position: absolute;
    left: 32px;
    top: 171px;
    list-style: none;
    color: var(--ink);
    font-size: 11.5px;
  }
  .contact-list li { display: flex; align-items: center; height: 17.6px; }
  .contact-list svg { width: 12px; height: 12px; margin-right: 8px; fill: var(--brown); }

  .address {
    position: absolute;
    right: 31px;
    top: 206px;
    text-align: right;
    color: var(--ink);
    font-size: 11.5px;
    font-style: normal;
    line-height: 17.6px;
  }

  .back-name {
    position: absolute;
    left: 0; right: 0;
    top: 96px;
    text-align: center;
    color: var(--white);
    font-size: 22px;
    font-weight: 700;
  }
  .services {
    position: absolute;
    left: 0; right: 0;
    top: 172px;
    text-align: center;
    color: var(--white);
    font-style: italic;
    font-size: 12px;
    line-height: 17.6px;
  }
  .services .dot, .credentials .dot { color: var(--orange); font-style: normal; }
  .credentials {
    position: absolute;
    left: 0; right: 0;
    top: 218px;
    text-align: center;
    color: var(--cream);
    font-size: 10.5px;
    line-height: 15px;
  }
</style>
</head>
<body>

  <section class="card card-front">
    <svg class="front-shape" viewBox="0 0 461 262" width="461" height="262" aria-hidden="true">
      <rect width="461" height="262" fill="var(--brown)"/>
      <path d="M0,46 C110,22 300,36 461,140 L461,262 L0,262 Z" fill="var(--paper)"/>
      <path d="M0,44 C110,20 300,34 461,138" fill="none" stroke="var(--orange)" stroke-width="4"/>
    </svg>

    <div class="holder">
      <p class="holder-name">Daniel Reyes</p>
      <p class="holder-title">CEO/Founder</p>
    </div>

    <p class="brand-name">Meadowlark Property Review</p>

    <ul class="contact-list">
      <li>
        <svg viewBox="0 0 12 12"><path d="M2.5 0.5 L4.5 0.5 L5.2 3.2 L3.8 4.3 C4.5 6 6 7.5 7.7 8.2 L8.8 6.8 L11.5 7.5 L11.5 9.5 C11.5 10.6 10.6 11.5 9.5 11.5 C4.5 11.5 0.5 7.5 0.5 2.5 C0.5 1.4 1.4 0.5 2.5 0.5 Z"/></svg>
        417 555 0182
      </li>
      <li>
        <svg viewBox="0 0 12 12"><rect x="3" y="0.5" width="6" height="3.5"/><rect x="0.5" y="4.5" width="11" height="5" rx="1"/><rect x="3" y="8.5" width="6" height="3" fill="var(--paper)" stroke="var(--brown)" stroke-width="1"/></svg>
        417 555 0193
      </li>
      <li>
        <svg viewBox="0 0 12 12"><rect x="0.5" y="2" width="11" height="8"/><path d="M0.5 2.5 L6 6.5 L11.5 2.5" fill="none" stroke="var(--paper)" stroke-width="1"/></svg>
        daniel@meadowlarkpr.com
      </li>
      <li>
        <svg viewBox="0 0 12 12"><circle cx="6" cy="6" r="5.5"/><path d="M6 0.5 C3.5 3 3.5 9 6 11.5 M6 0.5 C8.5 3 8.5 9 6 11.5 M0.5 6 L11.5 6" fill="none" stroke="var(--paper)" stroke-width="0.9"/></svg>
        www.meadowlarkpr.com
      </li>
    </ul>

    <address class="address">
      2210 Cedar Ridge Drive<br>
      Springfield, Missouri 65804
    </address>
  </section>

  <section class="card card-back">
    <p class="back-name">Meadowlark Property Review</p>
    <p class="services">
      Residential appraisals <span class="dot">•</span> Home inspection<br>
      Pest inspection and radon gas measurement.
    </p>
    <p class="credentials">
      State certified residential appraisal license <span class="dot">•</span> OBREX certified home inspector<br>
      Serving Springfield for 18 years
    </p>
  </section>

</body>
</html>
```